QVR business card

Need a business card for a company that provides instructional design and elearning development services. The website is here: http://quorvane.studio/

I'm attaching a current logo, as well as the old business card design. While I like to keep it clean, the old design is too simplistic for my liking. The only idea I want to reuse from the old design is placing industry jargon on the back of the card, just need a better way to present it. But if you have other ideas for the back--feel free to experiment.

Please use the colors complementary to the color we have on the website. Thank you!

```html
<!DOCTYPE html>
<html lang="en">
<head>
<meta charset="utf-8">
<title>QVR business card</title>
<link rel="stylesheet" href="https://fonts.googleapis.com/css2?family=Lato:wght@400;700&family=Montserrat:wght@700&family=Roboto+Condensed:wght@700&display=swap">
<style>
  :root {
    --teal: #14b2a8;
    --ink: #2b2b2b;
    --card-dark: #2a2a2b;
    --white: #ffffff;
    --stage: #e9e7e3;
  }
  * { margin: 0; padding: 0; box-sizing: border-box; }
  html, body {
    width: 1138px; height: 1200px; overflow: hidden;
    background: var(--stage);
  }
  .card {
    position: absolute;
    border-radius: 18px;
    overflow: hidden;
  }
  /* Front */
  .card-front {
    left: 218px; top: 198px; width: 671px; height: 384px;
    background: var(--white);
    font-family: "Lato", sans-serif;
  }
  .brand {
    position: absolute; left: 38px; top: 70px;
    display: flex; align-items: center; gap: 14px;
  }
  .brand-dot {
    width: 30px; height: 30px; border-radius: 50%;
    background: var(--teal);
  }
  .brand-name {
    font-size: 52px; font-weight: 700; color: var(--teal);
    letter-spacing: 2px; line-height: 1;
  }
  .contact-band {
    position: absolute; left: 0; right: 0; top: 220px; height: 132px;
    background: var(--teal);
    color: var(--white);
    padding: 16px 0 0 38px;
  }
  .person-name { font-size: 21px; font-weight: 700; line-height: 1.2; margin-bottom: 12px; }
  .contact-list { list-style: none; font-size: 18px; line-height: 23px; }
  .contact-list li { display: flex; align-items: center; gap: 8px; }
  .contact-list svg { width: 16px; height: 16px; flex: none; }

  /* Back */
  .card-back {
    left: 216px; top: 617px; width: 670px; height: 381px;
    background: var(--card-dark);
  }
  .jargon {
    position: absolute; left: 38px; width: 596px;
    font-family: "Montserrat", sans-serif; font-weight: 700;
    font-size: 35px; line-height: 1; color: var(--teal);
    letter-spacing: 1px;
    text-align: justify;
    text-align-last: justify;
  }
  .row-1 { top: 20px; }
  .row-2 { top: 68px; }
  .row-3 { top: 116px; }
  .row-4 { top: 228px; }
  .row-5 { top: 276px; }
  .row-6 { top: 324px; }
  .help-band {
    position: absolute; left: 0; right: 0; top: 159px; height: 58px;
    display: flex; align-items: center; justify-content: center;
  }
  .help-band::before, .help-band::after {
    content: ""; position: absolute; top: 0; bottom: 0; width: 22px;
    background: var(--white);
  }
  .help-band::before { left: 0; }
  .help-band::after { right: 0; }
  .help-text {
    font-family: "Roboto Condensed", sans-serif; font-weight: 700;
    font-size: 82px; line-height: 1; color: var(--white);
    letter-spacing: -5px; white-space: nowrap;
  }
</style>
</head>
<body>
  <section class="card card-front">
    <div class="brand">
      <span class="brand-dot"></span>
      <span class="brand-name">QVR</span>
    </div>
    <div class="contact-band">
      <p class="person-name">Dorian Vell</p>
      <ul class="contact-list">
        <li>
          <svg viewBox="0 0 16 16" aria-hidden="true"><path fill="#fff" d="M4 1.5l2.2 2.6-1.3 1.6c.7 1.9 2.1 3.6 3.9 4.6l1.6-1.3 2.6 2.2-1.3 2.3C6.6 13 2.6 8.5 1.9 3.1z"/></svg>
          <span>555-014-2273</span>
        </li>
        <li>
          <svg viewBox="0 0 16 16" aria-hidden="true"><rect x="1" y="3" width="14" height="10" fill="#fff"/><path d="M1 3l7 6 7-6" fill="none" stroke="#14b2a8" stroke-width="1.4"/></svg>
          <span>dvell@quorvane.studio</span>
        </li>
        <li>
          <svg viewBox="0 0 16 16" aria-hidden="true"><g fill="none" stroke="#fff" stroke-width="1.3"><circle cx="8" cy="8" r="6.5"/><ellipse cx="8" cy="8" rx="2.8" ry="6.5"/><path d="M1.5 8h13M2.5 4.8h11M2.5 11.2h11"/></g></svg>
          <span>www.quorvane.studio</span>
        </li>
      </ul>
    </div>
  </section>

  <section class="card card-back">
    <p class="jargon row-1">MOBILE LEARNING SCORM</p>
    <p class="jargon row-2">INSTRUCTIONAL DESIGN LMS</p>
    <p class="jargon row-3">MOOCS ELEARNING HTML5</p>
    <div class="help-band"><p class="help-text">HOW CAN WE HELP?</p></div>
    <p class="jargon row-4">ADULT LEARNING THEORY</p>
    <p class="jargon row-5">GAMIFICATION CLASSROOM</p>
    <p class="jargon row-6">XAPI BLENDED LEARNING</p>
  </section>
</body>
</html>
```